Business Card for Professional Photographer

I'm looking for an eye catching modern clean design that compliments my logo/ website fonts & colours.
I specialise in architecture, corporate & commercial photography so I'm marketing to professional clients rather than portrait / wedding clients.

I would prefer to not have a solid black design.

My logo brand guide is as follows :

Main front font. : Reislust
Main font colour : #fff
Slogan front font : Ubuntu Bold
Monogram front font : Venti Medium
Container colour : #fff

I need print ready files in pdf .png & .eps formats.

Included in the files below are some screen grabs as reference to font & colours etc.

```html
<!DOCTYPE html>
<html lang="en">
<head>
<meta charset="UTF-8">
<title>Fine Angle – Business Card</title>
<link href="https://fonts.googleapis.com/css2?family=Ubuntu:wght@300;400;700&family=Titillium+Web:wght@700&family=Roboto:wght@400&display=swap" rel="stylesheet">
<style>
  :root {
    --backdrop: #3b3b3d;
    --card: #18181a;
    --gold: #c9a24a;
    --gold-light: #e3c37a;
    --white: #f4f4f4;
    --tile-navy: #26354a;
    --tile-navy-deep: #1a2433;
    --tile-sand: #5c4a36;
    --tile-brown: #3f3226;
    --tile-slate: #45505f;
    --tile-slate-deep: #2c3440;
  }
  * { margin: 0; padding: 0; box-sizing: border-box; }
  html, body { width: 799px; height: 1200px; overflow: hidden; }
  body { background: var(--backdrop); position: relative; font-family: "Ubuntu", sans-serif; }

  .card {
    position: absolute;
    left: 50px;
    width: 699px;
    height: 400px;
    background: var(--card);
    border-radius: 4px;
    box-shadow: 0 14px 30px rgba(0,0,0,.45);
    overflow: hidden;
  }
  .card--front { top: 90px; }
  .card--back { top: 710px; }

  .photo-collage {
    position: absolute; inset: 0;
    display: grid;
    grid-template-columns: 190px 235px 1fr;
    grid-template-rows: 1fr 1fr;
    gap: 3px;
    background: var(--card);
  }
  .photo-tile { width: 100%; height: 100%; }
  .photo-tile--a { background: linear-gradient(160deg, var(--tile-slate) 0%, var(--tile-navy-deep) 100%); }
  .photo-tile--b { background: linear-gradient(200deg, var(--tile-navy) 0%, var(--tile-navy-deep) 100%); }
  .photo-tile--c { background: linear-gradient(180deg, var(--tile-sand) 0%, var(--tile-brown) 100%); }
  .photo-tile--d { background: linear-gradient(150deg, var(--tile-brown) 0%, #2a231d 100%); }
  .photo-tile--e { background: linear-gradient(135deg, var(--tile-slate-deep) 0%, var(--tile-slate) 60%, #8a8f96 100%); }
  .photo-tile--f { background: linear-gradient(200deg, var(--tile-sand) 0%, var(--tile-brown) 100%); }
  .collage-shade { position: absolute; inset: 0; background: rgba(12,12,14,.5); }

  .brand { position: absolute; display: flex; align-items: center; gap: 18px; }
  .brand__mark {
    width: 74px; height: 74px; border-radius: 50%;
    border: 4px solid var(--gold);
    flex: none;
  }
  .brand__name {
    font-family: "Ubuntu", sans-serif;
    font-weight: 300;
    letter-spacing: 5px;
    text-transform: uppercase;
    white-space: nowrap;
  }
  .brand__slogan {
    font-family: "Ubuntu", sans-serif;
    font-weight: 700;
    letter-spacing: 2.2px;
    white-space: nowrap;
  }

  .card--front .brand { left: 70px; top: 95px; align-items: flex-end; }
  .card--front .brand__mark { width: 120px; height: 120px; border-width: 5px; }
  .card--front .brand__name { color: var(--gold-light); font-size: 40px; line-height: 1; }
  .card--front .brand__slogan { color: var(--gold); font-size: 13px; margin-top: 6px; }
  .front-web {
    position: absolute; left: 100px; top: 295px;
    color: var(--gold-light); font-size: 20px; letter-spacing: 4px;
  }

  .person { position: absolute; left: 48px; top: 48px; }
  .person__name { font-family: "Titillium Web", sans-serif; font-weight: 700; color: var(--gold); font-size: 24px; line-height: 1.1; }
  .person__role { font-family: "Roboto", sans-serif; color: var(--white); font-size: 16px; }

  .contact-list { position: absolute; left: 48px; top: 200px; list-style: none; font-family: "Roboto", sans-serif; color: var(--white); font-size: 17px; }
  .contact-list li { display: flex; align-items: center; gap: 10px; height: 24px; }
  .contact-list svg { width: 14px; height: 14px; fill: var(--gold); flex: none; }
  .contact-list .address { margin-left: -24px; }

  .card--back .brand { right: 40px; bottom: 60px; flex-direction: column; align-items: flex-end; gap: 10px; }
  .card--back .brand__mark { width: 96px; height: 96px; margin-right: 90px; }
  .card--back .brand__name { color: var(--white); font-size: 34px; }
  .card--back .brand__slogan { color: var(--white); font-size: 12px; }
</style>
</head>
<body>

  <section class="card card--front">
    <div class="photo-collage">
      <div class="photo-tile photo-tile--a" role="img" aria-label="Photograph of an architectural detail"></div>
      <div class="photo-tile photo-tile--c" role="img" aria-label="Photograph of a sunlit interior"></div>
      <div class="photo-tile photo-tile--e" role="img" aria-label="Photograph of a modern building facade against the sky"></div>
      <div class="photo-tile photo-tile--b" role="img" aria-label="Photograph of a waterside scene"></div>
      <div class="photo-tile photo-tile--d" role="img" aria-label="Photograph of a commercial product setup"></div>
      <div class="photo-tile photo-tile--f" role="img" aria-label="Photograph of an office interior"></div>
    </div>
    <div class="collage-shade"></div>
    <div class="brand">
      <span class="brand__mark"></span>
      <div>
        <div class="brand__name">Fine Angle</div>
        <div class="brand__slogan">Architecture Corporate Commercial</div>
      </div>
    </div>
    <div class="front-web">www.fineangle.com.au</div>
  </section>

  <section class="card card--back">
    <div class="person">
      <div class="person__name">Owen Hartley</div>
      <div class="person__role">Photographer</div>
    </div>

    <ul class="contact-list">
      <li><svg viewBox="0 0 16 16"><path d="M2 5c0-2 2-3 6-3s6 1 6 3v1h-3V5H5v1H2zM4 7h8l2 7H2z"/></svg>0412555018</li>
      <li><svg viewBox="0 0 16 16"><path d="M1 3h14v10H1zM2 4l6 5 6-5v-.5H2z" fill-rule="evenodd"/></svg>info@fineangle.com.au</li>
      <li><svg viewBox="0 0 16 16"><circle cx="8" cy="8" r="7"/><path d="M1 8h14M8 1c-3 3-3 11 0 14M8 1c3 3 3 11 0 14" stroke="#18181a" stroke-width="1.2" fill="none"/></svg>www.fineangle.com.au</li>
      <li class="address">48 Harbour Rd Lorne Vic 3232</li>
    </ul>

    <div class="brand">
      <span class="brand__mark"></span>
      <div class="brand__name">Fine Angle</div>
      <div class="brand__slogan">Architecture Corporate Commercial</div>
    </div>
  </section>

</body>
</html>
```